Business Cards - Brightpath Horizon

need to design unique business card for my mortgage business. I need to design credit card style business card for my business or any unique idea that you might have

Target Market(s)

Home Loan customers

Industry/Entity Type

Mortgage Brokerage

Contact Information for Business Card

please design credit card style or very unique style business card

Colors

Designer to choose colors to be used in the design.

Requirements
Must have
• Name
• position
• Phone number
• fax number
• email address
• website address
• social media address
• All above fields will be provided once design in finalised

```html
<!DOCTYPE html>
<html lang="en">
<head>
<meta charset="utf-8">
<title>Brightpath Horizon – Business Card</title>
<link rel="stylesheet" href="https://fonts.googleapis.com/css2?family=Work+Sans:wght@400;500&display=swap">
<style>
  :root {
    --canvas-bg: #ececea;
    --card-white: #ffffff;
    --brand-navy: #2c3f94;
    --brand-sky: #2aa6df;
    --brand-orange: #f28a1f;
    --orange-shade: #e9821c;
    --text-dark: #2f2f2f;
    --text-mid: #4a4a4a;
    --shadow: 0 10px 24px rgba(0,0,0,0.18);
  }
  * { margin: 0; padding: 0; box-sizing: border-box; }
  html, body { width: 1200px; height: 1000px; overflow: hidden; }
  body { background: var(--canvas-bg); position: relative; font-family: "Work Sans", Arial, sans-serif; }

  .card {
    position: absolute; left: 254px; width: 667px; height: 380px;
    border-radius: 20px; overflow: hidden; box-shadow: var(--shadow);
  }
  .card-front { top: 100px; background: var(--card-white); }
  .card-back { top: 520px; background: var(--brand-orange); }

  .brand-name {
    position: absolute; font-family: "Work Sans", Arial, sans-serif; font-weight: 500;
    line-height: 1.1; letter-spacing: 1px; text-transform: uppercase;
  }
  .card-front .brand-name { left: 26px; top: 60px; font-size: 30px; color: var(--brand-navy); }
  .card-back .brand-name { left: 0; right: 0; top: 138px; text-align: center; font-size: 46px; color: var(--card-white); }

  .person-name {
    position: absolute; left: 26px; top: 180px; font-size: 24px; font-weight: 400;
    letter-spacing: 1.5px; color: var(--brand-sky);
  }
  .person-role { position: absolute; left: 26px; top: 214px; font-size: 15px; font-weight: 400; color: var(--text-dark); }
  .address { position: absolute; left: 26px; top: 248px; font-size: 15px; line-height: 21px; color: var(--text-mid); font-style: normal; }

  .contact-list { position: absolute; left: 26px; top: 298px; list-style: none; font-size: 15px; line-height: 20px; color: var(--text-mid); }
  .contact-list li { display: flex; align-items: center; gap: 9px; }
  .contact-list svg { width: 10px; height: 10px; flex: none; }

  .feature-art { position: absolute; }
  .card-front .feature-art {
    left: 300px; top: 14px; width: 362px; height: 360px; border-radius: 50% 50% 14px 14px / 60% 60% 14px 14px;
    background: radial-gradient(ellipse at 50% 35%, #4cb6e6 0%, var(--brand-sky) 70%);
  }
  .card-back .feature-art {
    left: 336px; top: 20px; width: 328px; height: 356px; border-radius: 50% 50% 10px 10px / 55% 55% 10px 10px;
    background: var(--orange-shade);
  }

  .back-web {
    position: absolute; left: 0; right: 0; top: 334px; text-align: center;
    font-size: 15px; letter-spacing: 1.5px; color: rgba(255,255,255,0.9);
  }
</style>
</head>
<body>

  <section class="card card-front">
    <div class="brand-name">Brightpath<br>Horizon</div>

    <div class="person-name">DANIEL HARPER</div>
    <div class="person-role">Founder</div>
    <address class="address">480 Oakridge Ave.<br>Lakeview, FL 33210</address>

    <ul class="contact-list">
      <li>
        <svg viewBox="0 0 10 10"><path d="M2 1 L4 3 L3 4 Q4 6 6 7 L7 6 L9 8 L8 9 Q3 9 1 2 Z" fill="var(--brand-sky)"/></svg>
        555-301-4826
      </li>
      <li>
        <svg viewBox="0 0 10 10"><rect x="0.8" y="2" width="8.4" height="6" fill="none" stroke="var(--brand-sky)" stroke-width="1.2"/><path d="M1 2.5 L5 5.5 L9 2.5" fill="none" stroke="var(--brand-sky)" stroke-width="1.2"/></svg>
        hello@brightpathhorizon.com
      </li>
      <li>
        <svg viewBox="0 0 10 10"><circle cx="5" cy="5" r="4" fill="none" stroke="var(--brand-sky)" stroke-width="1"/><path d="M1 5 H9 M5 1 Q2.5 5 5 9 M5 1 Q7.5 5 5 9" fill="none" stroke="var(--brand-sky)" stroke-width="0.9"/></svg>
        www.BrightpathHorizon.com
      </li>
    </ul>

    <div class="feature-art" role="img" aria-label="Large sky-blue tree illustration"></div>
  </section>

  <section class="card card-back">
    <div class="feature-art" role="img" aria-label="Faint tone-on-tone tree illustration"></div>
    <div class="brand-name">Brightpath<br>Horizon</div>
    <div class="back-web">www.brightpathhome.com</div>
  </section>

</body>
</html>
```